Cover Art Design for a Notebook

We are going to give away some note books to our marketing department and want an elegant art design for the cover. There is a theme centered around ABCD of marketing that we want to leverage in the design. So these letters should be prominent in the design. The ABCD stand for Agility, Boost, Customer, Data.

If you could Cleverly incorporate these words into the letters with a good design that would be good.

But please make the ABCD the focus of the artwork. The words associated with them should be subtle, in the background, visible but not the focus.

We are looking for stylish. We want people to feel proud of the ELEGANT DESIGN when they take out this notebook for business.

Also worth mentioning- We are a biotechnology company so if you incorporate elements in that theme in, on, or around the ABCD letters, it could be a good idea. As long as it doesn’t kill the rest of the design.

I will upload our logo for Kelvara Biolume Sciences later (you can see it online) and this will need to go in one corner.

Notebook will be A5 format. Image on front cover only. Need ASAP.

(Do not make baby blocks as we don’t want something that looks like a kids book)

Target Market(s)

business people who feel proud to pull out this notebook

Industry/Entity Type

Biotechnology

Colors
ec1f27
ffffff
000000

Requirements
Must have
• ELEGANT ART DESIGN USING ABCD
Nice to have
• see brief above
Should not have
• baby blocks

```html
<!DOCTYPE html>
<html lang="en">
<head>
<meta charset="utf-8">
<title>ABCD Notebook Cover</title>
<link rel="stylesheet" href="https://fonts.googleapis.com/css2?family=Inter:wght@400;500&display=swap">
<style>
:root {
  --brand-red: #ec1f27;
  --ink: #231f20;
  --paper: #ffffff;
  --tile: rgba(246, 244, 242, 0.78);
  --bg-top: #f6ece6;
  --bg-mid: #e4e4e6;
  --bg-low: #f0c9bf;
  --bg-bottom: #f7c9cf;
}
* { margin: 0; padding: 0; box-sizing: border-box; }
html, body { width: 846px; height: 1200px; overflow: hidden; }
body { font-family: "Inter", Helvetica, Arial, sans-serif; background: var(--paper); }
.cover { position: relative; width: 846px; height: 1200px; overflow: hidden; }
.cover-photo {
  position: absolute; inset: 0;
  background:
    radial-gradient(ellipse at 85% 20%, rgba(214, 120, 170, 0.45), transparent 40%),
    radial-gradient(ellipse at 10% 12%, rgba(250, 220, 200, 0.8), transparent 45%),
    radial-gradient(ellipse at 50% 85%, rgba(240, 180, 120, 0.5), transparent 55%),
    linear-gradient(180deg, var(--bg-top) 0%, var(--bg-mid) 45%, #d9cfd2 62%, var(--bg-low) 78%, var(--bg-bottom) 100%);
}
.brand-name {
  position: absolute; top: 100px; left: 0; right: 0; text-align: center;
  color: var(--ink); font-weight: 500; font-size: 28px; letter-spacing: 0; line-height: 1;
}
.grid {
  position: absolute; left: 147px; top: 194px; width: 552px; height: 552px;
  display: grid; grid-template-columns: 1fr 1fr; grid-template-rows: 1fr 1fr;
  border: 3px solid var(--brand-red);
}
.cell { position: relative; background: var(--tile); }
.cell:nth-child(1), .cell:nth-child(3) { border-right: 3px solid var(--brand-red); }
.cell:nth-child(1), .cell:nth-child(2) { border-bottom: 3px solid var(--brand-red); }
.letter {
  position: absolute; top: 4px; right: 18px;
  color: var(--brand-red); font-weight: 500; font-size: 156px; line-height: 1;
}
.word {
  position: absolute; left: 20px; bottom: 20px;
  color: var(--ink); font-size: 55px; font-weight: 400; letter-spacing: -1.5px; line-height: 1;
}
.cell:nth-child(3) .word { left: 12px; bottom: 16px; letter-spacing: -2px; }
.cell:nth-child(4) .word { bottom: 18px; }
</style>
</head>
<body>
<main class="cover">
  <div class="cover-photo" role="img" aria-label="Soft-focus close-up photograph of a clear laboratory well plate in warm pink, amber and grey light"></div>
  <header class="brand-name">Kelvara Biolume Sciences</header>
  <section class="grid">
    <div class="cell"><span class="letter">A</span><span class="word">Agile</span></div>
    <div class="cell"><span class="letter">B</span><span class="word">Boost</span></div>
    <div class="cell"><span class="letter">C</span><span class="word">Customer</span></div>
    <div class="cell"><span class="letter">D</span><span class="word">Data</span></div>
  </section>
</main>
</body>
</html>
```